Counselling business needs a DL brochure design ready for print next week!

My business is called Quiet Harbour Counselling. My name is Megan Trelawny and I'm a qualified Psychotherapist based in Sydney, Australia.

I need a DL brochure to promote my business. I like the idea of possibly incorporating a leaf/leaves and/or the colour green in a sophisticated, understated way in the DL design. I have attached a leaf image for reference. I am looking for a simple, elegant design overall. Not too many fonts, something which is easy to read and captures people's interest.

I need a print ready design - something that my local instant printer can use easily. I need a print ready PDF and original files too for the printer. I am anticipating that the design will be A4 folded to DL as it needs to fit into standard dimension plastic DL stands at various locations.

My business is focussed upon helping people overcome difficulties such as grief or anxiety. I also work with people to help them plan their life adventures. My business is different from the average counselling business. For example, I give my clients a beautiful thick stock postcard at the end of every session with takeaway learnings and insights which they've uncovered. That way, they can reflect upon those discoveries and capitalise upon them.

I have an office in a local wellness centre. The brochure will be showcased at the centre and in local medical centres and shops. The aim is that new prospects will pick up the brochure and be prompted to call me for a counselling appointment.

I have attached copy for my DL brochure and a competitor's DL for reference. I'm not seeking to emulate the competitor, but I thought that it could be a useful reference - the competitor DL is clear and easy to read. I need my photo to be included in the brochure, adjacent to the information about my background. I have attached a reference photo for use as a positional - a full size image will need to be dropped in as part of this job by the winning designer.

I do not have a company logo at the moment, but I need my business name and contact details repeated several times in the DL.
Updates

Hello. Thank you for your designs. I am so pleased to have received them. I will be in touch in the next 24 hours. Best, Megan

Industry/Entity Type

Business

```html
<!DOCTYPE html>
<html lang="en">
<head>
<meta charset="utf-8">
<title>Quiet Harbour Counselling – DL Brochure</title>
<link href="https://fonts.googleapis.com/css2?family=Jost:ital,wght@1,400;1,500;1,600&display=swap" rel="stylesheet">
<style>
  :root {
    --green: #8dbb45;
    --green-pale: #e9f2dc;
    --paper: #ffffff;
    --ink: #3a3a3a;
    --backdrop: #eeeeea;
    --photo-field: #a3c78f;
    --photo-session: #d9dcd8;
  }
  * { margin: 0; padding: 0; box-sizing: border-box; }
  html, body { width: 1200px; height: 861px; overflow: hidden; }
  body {
    background: var(--backdrop);
    font-family: "Jost", "Futura", sans-serif;
    font-style: italic;
    color: var(--ink);
    position: relative;
  }
  .brochure {
    position: absolute; left: 44px; top: 38px;
    width: 1111px; height: 785px;
    display: flex;
  }
  .panel { position: relative; height: 100%; }
  .panel--inside { width: 370px; background: var(--paper); }
  .panel--back { width: 371px; background: var(--green); color: #fff; }
  .panel--cover { width: 370px; background: var(--paper); }

  /* inside panel */
  .deco-circle {
    position: absolute; left: 10px; top: 180px;
    width: 350px; height: 350px; border-radius: 50%;
    background: var(--green-pale);
  }
  .questions {
    position: relative; padding-top: 60px;
    display: flex; flex-direction: column; align-items: center; gap: 17px;
    text-align: center; font-size: 16.5px; font-weight: 500; line-height: 23px;
  }
  .photo { position: absolute; }
  .photo--session {
    left: 27px; top: 590px; width: 314px; height: 168px;
    background: var(--photo-session);
  }

  /* back panel */
  .tagline {
    position: absolute; top: 180px; left: 0; width: 100%;
    text-align: center; font-size: 21px; font-weight: 600; line-height: 32px;
  }
  .ribbon {
    position: absolute; background: var(--paper); color: var(--green);
    font-size: 24px; font-weight: 600;
    display: flex; align-items: center; justify-content: center;
  }
  .ribbon--top { left: 40px; top: 271px; width: 291px; height: 46px; }
  .ribbon--bottom { left: 51px; top: 322px; width: 270px; height: 45px; }
  .brand {
    position: absolute; display: flex; align-items: center; gap: 12px;
    font-weight: 600; text-transform: uppercase; line-height: 1.15;
    white-space: nowrap;
  }
  .brand__dot { flex: none; border-radius: 50%; }
  .brand--back { left: 50%; transform: translateX(-50%); top: 532px; color: #fff; font-size: 19px; }
  .brand--back .brand__dot { width: 66px; height: 66px; background: #fff; }
  .contact {
    position: absolute; left: 0; width: 100%;
    display: flex; justify-content: center; align-items: center; gap: 6px;
    font-weight: 600; white-space: nowrap;
  }
  .contact--phone { top: 645px; font-size: 22px; }
  .contact--email { top: 687px; font-size: 16px; }
  .contact--web { top: 722px; font-size: 16px; }
  .contact svg { fill: #fff; }

  /* cover panel */
  .cover-heading {
    position: absolute; left: 29px; top: 35px;
    color: var(--green); font-size: 26px; font-weight: 600; line-height: 42px;
  }
  .cover-badge {
    position: absolute; left: 256px; top: 35px; width: 78px; height: 78px;
    border-radius: 50%; background: var(--green-pale);
  }
  .photo--field {
    left: 29px; top: 204px; width: 313px; height: 381px;
    background: var(--photo-field);
  }
  .brand--cover { left: 52px; top: 623px; color: var(--green); font-size: 22px; }
  .brand--cover .brand__dot { width: 80px; height: 80px; background: var(--green); }
  .cover-web {
    position: absolute; left: 0; top: 726px; width: 100%;
    text-align: center; font-size: 16px; font-weight: 600; color: var(--ink);
  }
</style>
</head>
<body>
<main class="brochure">

  <section class="panel panel--inside">
    <div class="deco-circle" aria-hidden="true"></div>
    <div class="questions">
      <p>DO YOU NEED<br>A POSITIVE CHANGE?</p>
      <p>DO YOU WISH You felt<br>more joyful and fulfilled?</p>
      <p>You felt less stressed<br>or overwhelmed?</p>
      <p>You coped better with<br>life’s challenges?</p>
      <p>You could break unhelpful habits?</p>
      <p>DO YOU IMAGINE Your<br>relationships being closer?</p>
      <p>Your life being well balanced?</p>
      <p>Your goals being within reach?</p>
      <p>Your life being more adventurous?</p>
    </div>
    <div class="photo photo--session" role="img" aria-label="Photo of a client talking with a counsellor who holds a clipboard"></div>
  </section>

  <section class="panel panel--back">
    <p class="tagline">The Power To Create New<br>Possibilities Is Within You</p>
    <div class="ribbon ribbon--top">You Might Just Need</div>
    <div class="ribbon ribbon--bottom">A Helping Hand</div>
    <div class="brand brand--back">
      <span class="brand__dot" aria-hidden="true"></span>
      <span>Quiet Harbour<br>Counselling</span>
    </div>
    <p class="contact contact--phone">
      <svg width="18" height="20" viewBox="0 0 24 24" aria-hidden="true"><path d="M6.6 10.8a15.1 15.1 0 0 0 6.6 6.6l2.2-2.2a1 1 0 0 1 1-.25 11.4 11.4 0 0 0 3.6.57 1 1 0 0 1 1 1V20a1 1 0 0 1-1 1A17 17 0 0 1 3 4a1 1 0 0 1 1-1h3.5a1 1 0 0 1 1 1c0 1.25.2 2.45.57 3.57a1 1 0 0 1-.25 1z"/></svg>
      0400 512 377
    </p>
    <p class="contact contact--email">
      <svg width="15" height="11" viewBox="0 0 20 14" aria-hidden="true"><path d="M0 0h20v14H0z M1.5 1.5 10 8l8.5-6.5" fill="#fff" stroke="var(--green)" stroke-width="1.5"/></svg>
      hello@quietharbourcounselling.com
    </p>
    <p class="contact contact--web">
      <svg width="14" height="14" viewBox="0 0 20 20" aria-hidden="true"><circle cx="10" cy="10" r="8.5" fill="none" stroke="#fff" stroke-width="1.6"/><path d="M1.5 10h17M10 1.5c-4 4.5-4 12.5 0 17M10 1.5c4 4.5 4 12.5 0 17" fill="none" stroke="#fff" stroke-width="1.4"/></svg>
      www.quietharbourcounselling.com
    </p>
  </section>

  <section class="panel panel--cover">
    <h1 class="cover-heading">Overcome<br>Difficulties and<br>Make A Fresh Start</h1>
    <div class="cover-badge" aria-hidden="true"></div>
    <div class="photo photo--field" role="img" aria-label="Photo of a man outdoors with arms raised in celebration"></div>
    <div class="brand brand--cover">
      <span class="brand__dot" aria-hidden="true"></span>
      <span>Quiet Harbour<br>Counselling</span>
    </div>
    <p class="cover-web">www.quietharbourcounselling.com</p>
  </section>

</main>
</body>
</html>
```